Redesign of the UI of a customer service platform

To improve the user experience of our customers, we need a new design for our agent interface of our customer service platform (quillnest.com).
The focus will be on the dashboard and the inbox screens (see attached) along with the common UI elements (Buttons, menu, fonts, forms...)
We want a simple and distinctive design

Target Market(s)

Worldwide

Industry/Entity Type

It Service

Number of Pages Required

3 page

Font styles to use
Sans Serif

Requirements
Must have
• New Onboarding page: this is a new page that is shown to user the first time they login to the platform. This will replace the current onboarding screen (setup SMS, Setup widget...etc)
• Dashboard page: to access important information and activate services (see screenshot from current site)
• Inbox page: to manage all the interactions with customers. (see screenshot from current site)
• UI elements (buttons, menus, forms, tables, fonts, color palette)

```html
<!DOCTYPE html>
<html lang="en">
<head>
<meta charset="utf-8">
<title>quillnest — Inbox</title>
<link rel="stylesheet" href="https://fonts.googleapis.com/css2?family=Open+Sans:wght@300;400;600;700&display=swap">
<style>
:root{
  --orange:#f05023;
  --orange-active:#b9391a;
  --topbar:#2b2b2b;
  --blue:#1a9bf0;
  --navy-1:#0d2d40;
  --navy-2:#1d506c;
  --text:#333;
  --muted:#8a8a8a;
  --line:#dcdcdc;
  --soft:#f0f0f0;
  --footer:#e6e6e6;
  --green:#5dc84a;
  --avatar:#b9a99a;
}
*{box-sizing:border-box;margin:0;padding:0}
html,body{width:1200px;height:792px;overflow:hidden}
body{position:relative;font-family:"Open Sans",Arial,sans-serif;color:var(--text);background:#fff}
.abs{position:absolute}
.topbar{left:0;top:0;width:1200px;height:84px;background:var(--topbar);color:#fff}
.burger{left:55px;top:40px;width:28px}
.burger span{display:block;height:3px;background:#fff;margin-bottom:5px}
.brand{left:100px;top:32px;display:flex;align-items:center;gap:6px;font-weight:700;font-size:19px;color:#fff}
.brand i{width:16px;height:16px;border-radius:50%;background:#fff;display:block}
.top-icons{left:682px;top:34px;display:flex;gap:20px}
.status{left:822px;top:37px;font-size:13px;display:flex;align-items:center;gap:6px}
.status i{width:9px;height:9px;border-radius:50%;background:var(--green)}
.user{left:944px;top:28px;display:flex;align-items:center;gap:8px;font-size:13px}
.avatar{border-radius:50%;background:var(--avatar);display:block;flex:none}
.sidebar{left:0;top:84px;width:245px;height:639px;background:var(--orange)}
.nav-item{height:50px;display:flex;align-items:center;padding-left:46px;gap:17px;color:#fff;font-size:18px;font-weight:300;border-bottom:1px solid rgba(0,0,0,.08)}
.nav-item:first-child{height:61px;padding-top:14px}
.nav-item.active{background:var(--orange-active);height:54px}
.nav-item svg{width:28px;height:28px}
.footer{left:0;top:723px;width:1200px;height:69px;background:var(--footer);font-size:11px;color:#888;text-align:center;padding-top:25px}
.page-title{left:273px;top:110px;font-size:26px;font-weight:300;color:#333}
.panel{left:274px;top:162px;width:863px;height:503px;border:1px solid var(--line)}
.tabs{left:0;top:0;width:861px;height:38px;background:#f3f3f3;border-bottom:1px solid var(--line)}
.tab{top:0;height:38px;font-size:17px;font-weight:300;color:#555;padding-top:9px}
.tab sup{font-size:11px}
.tab.active{background:var(--blue);color:#fff;left:0;width:90px;padding-left:20px}
.list{left:0;top:38px;width:364px;height:463px;border-right:1px solid var(--line)}
.item{left:0;width:363px;border-bottom:1px solid var(--line)}
.item.current{background:linear-gradient(var(--navy-2),var(--navy-1));color:#fff;border:none}
.item .avatar{position:absolute;left:23px;width:36px;height:36px}
.num{position:absolute;left:67px;font-size:11px;color:#888}
.name{position:absolute;left:91px;font-size:14px}
.snip{position:absolute;left:91px;font-size:11px;color:#888}
.when{position:absolute;left:258px;font-size:11px;color:#666;display:flex;gap:6px;align-items:center}
.current .num,.current .snip,.current .when{color:#fff}
.done{left:95px;top:380px;width:170px;text-align:center;font-size:12px;color:#aaa}
.done .rule{display:flex;align-items:center;gap:10px}
.done .rule::before,.done .rule::after{content:"";flex:1;height:1px;background:#ccc}
.done small{display:block;font-size:11px;margin-top:4px}
.convo-title{left:387px;top:50px;font-size:17px;color:#444}
.btn{top:51px;height:26px;border:1px solid #ccc;font-size:12px;color:#888;display:flex;align-items:center;gap:5px;padding:0 10px;background:#fff}
.chat{left:389px;top:87px;width:454px;height:250px;border:1px solid var(--line)}
.chat-bar{left:0;top:0;width:452px;height:28px;background:var(--orange);color:#fff;font-size:11px;font-weight:600;padding:7px 14px}
.chat-bar span{position:absolute;right:30px;top:8px;font-size:9px;font-weight:400;opacity:.85}
.bubble{background:var(--soft);font-size:12px;color:#888;padding:10px 13px}
.input{left:0;top:216px;width:452px;height:32px;border-top:1px solid var(--line);background:#f8f8f8;font-size:12px;color:#999;padding:8px 20px}
.input b{position:absolute;right:14px;top:6px;color:#aaa;font-weight:400}
.dtabs{left:363px;top:353px;width:498px;height:37px;background:#f3f3f3;border-top:1px solid var(--line);border-bottom:1px solid var(--line)}
.dtab{top:0;height:36px;font-size:14px;color:#777;display:flex;align-items:center;gap:5px}
.dtab.active{background:var(--blue);color:#fff;left:0;width:96px;padding-left:13px}
.details{font-size:11px;color:#444;line-height:19.5px}
.edit{left:1066px;top:560px;width:63px;height:25px;border:1px solid var(--green);color:var(--green);font-size:12px;display:flex;align-items:center;justify-content:center;gap:4px;background:#fff}
</style>
</head>
<body>
<header class="abs topbar">
  <div class="abs burger"><span></span><span></span><span></span></div>
  <div class="abs brand"><i></i>quillnest</div>
  <div class="abs top-icons">
    <svg width="24" height="22" viewBox="0 0 24 22"><ellipse cx="12" cy="10" rx="11" ry="8" fill="#555"/><path d="M5 15l-2 6 7-4z" fill="#555"/></svg>
    <svg width="26" height="24" viewBox="0 0 26 24"><rect x="5" y="5" width="16" height="12" rx="2" transform="rotate(-40 13 11)" fill="none" stroke="#555" stroke-width="3"/></svg>
    <svg width="24" height="24" viewBox="0 0 24 24"><circle cx="12" cy="12" r="11" fill="#555"/><text x="12" y="17" text-anchor="middle" font-size="15" font-weight="700" fill="#2b2b2b" font-family="Open Sans,sans-serif">?</text></svg>
  </div>
  <div class="abs status"><i></i>Available <svg width="12" height="8" viewBox="0 0 12 8"><path d="M1 1l5 5 5-5" stroke="#777" fill="none"/></svg></div>
  <div class="abs user"><span class="avatar" role="img" aria-label="Agent profile photo" style="width:30px;height:30px"></span>Omar Reyes <svg width="12" height="8" viewBox="0 0 12 8"><path d="M1 1l5 5 5-5" stroke="#777" fill="none"/></svg></div>
</header>

<nav class="abs sidebar">
  <div class="nav-item"><svg viewBox="0 0 28 28"><path d="M2 22a12 12 0 0 1 24 0z" fill="#fff" opacity=".85"/><circle cx="14" cy="20" r="2.5" fill="var(--orange)"/><path d="M14 20l5-8" stroke="var(--orange)" stroke-width="2"/></svg>Dashboard</div>
  <div class="nav-item active"><svg viewBox="0 0 28 28"><rect x="1" y="5" width="26" height="18" rx="2" fill="#fff"/><path d="M2 7l12 9 12-9" stroke="var(--orange-active)" stroke-width="2" fill="none"/></svg>Inbox</div>
  <div class="nav-item"><svg viewBox="0 0 28 28"><rect x="6" y="8" width="16" height="12" rx="2" transform="rotate(-40 14 14)" fill="none" stroke="#fff" stroke-width="3" opacity=".85"/></svg>Tickets</div>
  <div class="nav-item"><svg viewBox="0 0 28 28" fill="#fff" opacity=".85"><circle cx="8" cy="8" r="4"/><circle cx="20" cy="8" r="4"/><circle cx="14" cy="12" r="4"/><path d="M2 22a6 6 0 0 1 12-6 6 6 0 0 1 12 6v3H2z"/></svg>Clients</div>
  <div class="nav-item"><svg viewBox="0 0 28 28" fill="#fff" opacity=".85"><path d="M13 3a11 11 0 1 0 11 12H13z"/><path d="M16 1v11h11A11 11 0 0 0 16 1z"/></svg>Reports</div>
  <div class="nav-item"><svg viewBox="0 0 28 28"><circle cx="14" cy="14" r="9" fill="none" stroke="#fff" stroke-width="5" stroke-dasharray="4 3" opacity=".85"/><circle cx="14" cy="14" r="6" fill="#fff" opacity=".85"/><circle cx="14" cy="14" r="3" fill="var(--orange)"/></svg>Settings</div>
</nav>

<h1 class="abs page-title">Inbox</h1>

<section class="abs panel">
  <div class="abs tabs">
    <div class="abs tab active">Agents<sup>4</sup></div>
    <div class="abs tab" style="left:108px">Department</div>
    <div class="abs tab" style="left:239px">Account <sup>4</sup></div>
  </div>

  <div class="abs list">
    <div class="abs item current" style="top:0;height:67px">
      <span class="avatar" role="img" aria-label="Customer photo" style="top:13px"></span>
      <span class="num" style="top:23px;font-weight:600">#4</span>
      <span class="name" style="top:17px">Nora Kellwyn</span>
      <span class="snip" style="top:41px">Hello</span>
      <span class="when" style="top:22px"><svg width="18" height="14" viewBox="0 0 18 14"><path d="M2 2h10v7H6l-3 3V9H2z M12 5h4v6h-1v2l-2-2H8" fill="none" stroke="var(--blue)" stroke-width="1.5"/></svg>21 days ago</span>
    </div>
    <div class="abs item" style="top:67px;height:88px">
      <span class="avatar" role="img" aria-label="Customer photo" style="top:26px"></span>
      <span class="num" style="top:35px">#3</span>
      <span class="name" style="top:29px">JonMarlowe</span>
      <span class="snip" style="top:55px">How are you</span>
      <span class="when" style="top:34px"><svg width="18" height="14" viewBox="0 0 18 14"><path d="M2 2h10v7H6l-3 3V9H2z M12 5h4v6h-1v2l-2-2H8" fill="none" stroke="var(--blue)" stroke-width="1.5"/></svg>25 days ago</span>
    </div>
    <div class="abs item" style="top:155px;height:83px">
      <span class="avatar" role="img" aria-label="Customer photo" style="top:22px"></span>
      <span class="num" style="top:31px">#2</span>
      <span class="name" style="top:25px">Ivy Tarrenfield</span>
      <span class="snip" style="top:51px">This is testy message from the</span>
      <span class="when" style="top:30px"><svg width="18" height="14" viewBox="0 0 18 14"><path d="M2 2h10v7H6l-3 3V9H2z M12 5h4v6h-1v2l-2-2H8" fill="none" stroke="var(--blue)" stroke-width="1.5"/></svg>a month ago</span>
    </div>
    <div class="abs item" style="top:238px;height:80px;border:none">
      <span class="avatar" role="img" aria-label="Customer photo" style="top:19px"></span>
      <span class="num" style="top:28px">#1</span>
      <span class="name" style="top:22px">Omar Belcourt</span>
      <span class="when" style="top:27px"><svg width="18" height="14" viewBox="0 0 18 14"><path d="M2 2h10v7H6l-3 3V9H2z M12 5h4v6h-1v2l-2-2H8" fill="none" stroke="var(--blue)" stroke-width="1.5"/></svg>a month ago</span>
    </div>
    <div class="abs done"><div class="rule">DONE</div><small>No Recent Clients</small></div>
  </div>

  <h2 class="abs convo-title" style="font-weight:400">#4 Nora Kellwyn</h2>
  <div class="abs btn" style="left:629px;width:63px">
    <svg width="13" height="11" viewBox="0 0 13 11"><ellipse cx="6.5" cy="5" rx="6" ry="4.5" fill="#ccc"/></svg>Chat</div>
  <div class="abs btn" style="left:698px;width:80px">
    <svg width="13" height="11" viewBox="0 0 13 11"><path d="M1 10c0-5 3-6 8-6V1l4 4-4 4V6c-4 0-6 1-8 4z" fill="#bbb"/></svg>Transfer</div>
  <div class="abs btn" style="left:781px;width:62px">
    <svg width="12" height="12" viewBox="0 0 12 12"><circle cx="6" cy="6" r="5" fill="none" stroke="#bbb" stroke-width="1.5"/><path d="M3 9l6-6" stroke="#bbb" stroke-width="1.5"/></svg>Ban</div>

  <div class="abs chat">
    <div class="abs chat-bar">More Details<span>Save Transcript</span></div>
    <span class="abs avatar" role="img" aria-label="Customer photo" style="left:16px;top:40px;width:44px;height:44px"></span>
    <div class="abs bubble" style="left:70px;top:42px;width:366px;height:68px">Hello</div>
    <span class="abs avatar" role="img" aria-label="Agent photo" style="left:320px;top:124px;width:36px;height:36px"></span>
    <div class="abs bubble" style="left:366px;top:123px;width:70px;height:36px">Hello</div>
    <div class="abs input">Type message here<b>›</b></div>
  </div>

  <div class="abs dtabs">
    <div class="abs dtab active"><svg width="16" height="16" viewBox="0 0 16 16"><rect x="1" y="4" width="9" height="11" fill="none" stroke="#fff" stroke-width="1.5"/><rect x="6" y="1" width="9" height="11" fill="none" stroke="#fff" stroke-width="1.5"/></svg>Details</div>
    <div class="abs dtab" style="left:108px"><svg width="18" height="16" viewBox="0 0 18 16"><rect x="4" y="4" width="11" height="8" rx="1" transform="rotate(-40 9 8)" fill="none" stroke="#aaa" stroke-width="2"/></svg>Tickets</div>
    <div class="abs dtab" style="left:197px"><svg width="16" height="16" viewBox="0 0 16 16"><circle cx="8" cy="8" r="7" fill="none" stroke="#aaa" stroke-width="1.5"/><path d="M8 4v4h3" stroke="#aaa" stroke-width="1.5" fill="none"/></svg>History</div>
  </div>

  <div class="abs details" style="left:391px;top:415px"><div style="font-size:12px">Nora Kellwyndale</div><div>Email</div><div>Phone</div></div>
  <div class="abs details" style="left:598px;top:416px"><div>Address</div><div>City Town</div><div>Country</div></div>
</section>

<div class="abs edit"><svg width="13" height="12" viewBox="0 0 13 12"><rect x="1" y="2" width="9" height="9" fill="none" stroke="var(--green)" stroke-width="1.3"/><path d="M5 7l6-6" stroke="var(--green)" stroke-width="1.6"/></svg>Edit</div>

<footer class="abs footer">© 2017 Company Name&nbsp; All right reserved&nbsp; Term of Use</footer>
</body>
</html>
```